Travel Agency Website - Simple General

Need a 7 page simple design that is pretty repetitive. Need to be able to load quickly that is SEO optimized. Trying to give ideas on what they can do, be personal as we are local, but at the same time come across as professional and get information easily with little burden.

- Landing Page
- Brimwell Vacations Page
- Family Trips
- Road Trips from Texas
- Other Destinations
- About Us Page
- Contact Us Page

Target Market(s)

Families

Coding

Coded - Design and coding required

Number of Pages Required

5+ page

Colors

Designer to choose colors to be used in the design.

Requirements
Must have
• Like it to flow easily with our logo. Use that for colors, etc.

```html
<!DOCTYPE html>
<html lang="en">
<head>
<meta charset="utf-8">
<title>Wanderbright Travel Co. – Family Travel Planning</title>
<link href="https://fonts.googleapis.com/css2?family=Playfair+Display:wght@700;800&family=Lato:wght@400;700&display=swap" rel="stylesheet">
<style>
:root{
  --teal:#0f6b6e;
  --navy:#0b1f3a;
  --gold:#b8650f;
  --ink:#1c2330;
  --white:#ffffff;
  --cream:#f7f3ec;
}
*{box-sizing:border-box;margin:0;padding:0}
html,body{width:667px;height:1200px;overflow:hidden}
body{font-family:"Lato",sans-serif;color:var(--ink);background:var(--white);position:relative}
.abs{position:absolute}
.topbar{left:246px;top:0;width:421px;height:19px;background:var(--teal);clip-path:polygon(5px 0,100% 0,100% 100%,0 100%);color:var(--white);font-size:8px}
.topbar .item{position:absolute;top:0;height:19px;display:flex;align-items:center;gap:6px}
.social{display:flex;gap:4px}
.social span{width:12px;height:12px;border-radius:50%;background:var(--white);display:block}
.brand{left:60px;top:12px;height:44px;display:flex;align-items:center;gap:5px}
.brand .dot{width:9px;height:9px;border-radius:50%;background:var(--gold)}
.brand-name{font-family:"Playfair Display",serif;font-weight:700;color:var(--teal);font-size:11px;line-height:1.15}
.nav{left:162px;top:37px;display:flex;gap:17px;font-size:8.3px;color:var(--ink)}
.nav a{color:inherit;text-decoration:none}
.nav .active{color:var(--teal);text-decoration:underline}
.hero{left:0;top:67px;width:667px;height:333px;background:
  radial-gradient(ellipse 120px 70px at 450px 120px,rgba(255,236,190,.85),transparent 70%),
  radial-gradient(ellipse 90px 150px at 520px 210px,rgba(240,225,200,.55),transparent 70%),
  radial-gradient(ellipse 110px 90px at 60px 270px,rgba(120,90,50,.8),transparent 70%),
  linear-gradient(180deg,rgba(60,80,40,.55) 0%,transparent 40%,rgba(90,60,35,.5) 100%),
  linear-gradient(100deg,#4a3826 0%,#8e6a42 30%,#e5c08a 55%,#b98a55 78%,#4f3f28 100%)}
.hero-panel{left:86px;top:164px;width:289px;height:158px;background:rgba(45,45,45,.55);border-radius:12px;text-align:center;color:var(--white)}
.hero-panel h1{font-family:"Playfair Display",serif;font-weight:700;font-size:29px;line-height:36px;margin-top:7px;text-shadow:0 1px 3px rgba(0,0,0,.4)}
.hero-panel p{font-size:10px;font-weight:700;line-height:14.5px;margin-top:7px}
.btn{display:inline-flex;align-items:center;justify-content:center;background:var(--navy);color:var(--white);font-weight:700;border-radius:14px;text-decoration:none}
.hero-panel .btn{width:115px;height:27px;font-size:10px;border:1px solid var(--white);margin-top:10px}
.featured{left:0;top:400px;width:667px;height:330px;background:
  radial-gradient(ellipse 160px 120px at 600px 80px,rgba(190,200,170,.35),transparent 70%),
  radial-gradient(ellipse 200px 120px at 80px 60px,rgba(200,190,160,.3),transparent 70%),
  linear-gradient(180deg,#faf6ef,#efe6d6 60%,#fbf8f2)}
.section-title{font-family:"Playfair Display",serif;font-weight:700;font-size:25px;color:var(--navy)}
.section-title em{font-style:normal;color:var(--teal)}
.rule{height:2px;background:var(--gold)}
.card{top:497px;width:129px;height:149px;background:var(--white);border-radius:10px;box-shadow:0 1px 4px rgba(0,0,0,.2);padding:3px}
.card .photo{height:122px;border-radius:9px}
.card .label{display:flex;justify-content:space-between;align-items:center;padding:6px 9px 0 9px;font-family:"Playfair Display",serif;font-weight:700;font-size:9px;color:var(--navy)}
.about-photo{left:60px;top:729px;width:267px;height:186px;border-radius:6px;background:
  radial-gradient(ellipse 70px 40px at 45px 85px,rgba(255,230,170,.95),transparent 70%),
  linear-gradient(180deg,#f3d7a6,#eab27a 42%,#d4a27a 55%,#9fa3a6 72%,#6d7884)}
.about-text{left:358px;top:795px;width:247px;font-size:8.2px;line-height:14.3px;text-align:justify;color:var(--ink)}
.about .btn{left:358px;top:872px;width:77px;height:26px;font-size:10px}
.footer{left:0;top:962px;width:667px;height:238px;background:
  radial-gradient(ellipse 150px 110px at 600px 60px,rgba(40,70,90,.6),transparent 70%),
  radial-gradient(ellipse 150px 110px at 60px 150px,rgba(40,70,90,.5),transparent 70%),
  linear-gradient(180deg,#1a2d45,#0f2036)}
.foot-brand{left:286px;top:1016px;width:95px;height:80px;border-radius:14px;background:var(--cream);display:flex;align-items:center;justify-content:center}
.foot-nav{left:0;top:1111px;width:667px;display:flex;justify-content:center;gap:17px;font-size:8.3px;color:var(--white)}
.foot-contact{top:1143px;font-size:8.3px;display:flex;align-items:center;gap:6px;color:var(--white)}
.foot-rule{left:61px;top:1172px;width:544px;height:1px;background:rgba(255,255,255,.25)}
.copy{right:62px;top:1180px;font-size:8.3px;color:var(--white)}
</style>
</head>
<body>

<div class="abs topbar">
  <div class="item" style="left:34px">
    <svg width="10" height="10" viewBox="0 0 24 24"><path fill="#fff" d="M6.6 10.8a15 15 0 0 0 6.6 6.6l2.2-2.2c.3-.3.7-.4 1-.2 1.1.4 2.3.6 3.6.6.6 0 1 .4 1 1V20c0 .6-.4 1-1 1A17 17 0 0 1 3 4c0-.6.4-1 1-1h3.5c.6 0 1 .4 1 1 0 1.3.2 2.5.6 3.6.1.3 0 .7-.2 1z"/></svg>
    <span>111.111.1111</span>
  </div>
  <div class="item" style="left:141px">
    <svg width="10" height="8" viewBox="0 0 20 14"><rect x="1" y="1" width="18" height="12" fill="none" stroke="#fff" stroke-width="1.6"/><path d="M1 1l9 7 9-7" fill="none" stroke="#fff" stroke-width="1.6"/></svg>
    <span>hello@wanderbrighttravel.com</span>
  </div>
  <div class="item social" style="left:331px"><span></span><span></span></div>
</div>

<div class="abs brand"><span class="dot"></span><span class="brand-name">Wanderbright<br>Travel Co.</span></div>

<nav class="abs nav">
  <a class="active" href="#">Home</a>
  <a href="#">Brimwell Vacations</a>
  <a href="#">Family Trips</a>
  <a href="#">Texas Road Trips</a>
  <a href="#">Other Destinations</a>
  <a href="#">About Us</a>
  <a href="#">Contact Us</a>
</nav>

<section class="abs hero" role="img" aria-label="Family with luggage walking toward a sunlit tropical resort, suitcase and straw hat in the foreground"></section>
<div class="abs hero-panel">
  <h1>Where Every Journey Begins with a Dream</h1>
  <p>Magical escapes, family memories, and adventures<br>made just for you</p>
  <a class="btn" href="#">Start Your Journey</a>
</div>

<section class="abs featured" role="img" aria-label="Faded beach and palm trees background"></section>
<h2 class="abs section-title" style="left:0;top:440px;width:667px;text-align:center">Featured <em>Experiences</em></h2>
<div class="abs rule" style="left:297px;top:476px;width:74px"></div>

<div class="abs card" style="left:61px">
  <div class="photo" role="img" aria-label="Fairytale castle under a blue sky with clouds" style="background:radial-gradient(ellipse 50px 45px at 62px 80px,rgba(220,225,235,.9),transparent 70%),radial-gradient(ellipse 40px 25px at 20px 75px,rgba(255,255,255,.8),transparent 70%),linear-gradient(180deg,#163f86,#3c68ad 45%,#9aa9c2 75%,#7b6f60)"></div>
  <div class="label"><span>Brimwell Vacations</span><svg width="12" height="12" viewBox="0 0 12 12"><circle cx="6" cy="6" r="5.3" fill="none" stroke="#555" stroke-width=".8"/><path d="M3.5 6h5M6.5 4l2 2-2 2" fill="none" stroke="#555" stroke-width=".8"/></svg></div>
</div>
<div class="abs card" style="left:200px">
  <div class="photo" role="img" aria-label="Family cheering on a car roof by the sea" style="background:radial-gradient(ellipse 55px 30px at 70px 70px,rgba(230,200,170,.8),transparent 70%),linear-gradient(180deg,#4fa8dc,#8ccbea 40%,#3d9fd0 60%,#2a8fd0 80%,#1a5f96)"></div>
  <div class="label"><span>Family Trips</span><svg width="12" height="12" viewBox="0 0 12 12"><circle cx="6" cy="6" r="5.3" fill="none" stroke="#555" stroke-width=".8"/><path d="M3.5 6h5M6.5 4l2 2-2 2" fill="none" stroke="#555" stroke-width=".8"/></svg></div>
</div>
<div class="abs card" style="left:338px">
  <div class="photo" role="img" aria-label="Winding Texas highway through green hills at sunset" style="background:radial-gradient(ellipse 30px 70px at 70px 100px,rgba(70,75,85,.9),transparent 70%),linear-gradient(180deg,#f0a24a,#e8b46a 22%,#7d8a4a 40%,#55703a 65%,#4a4f55)"></div>
  <div class="label"><span>Texas Road Trips</span><svg width="12" height="12" viewBox="0 0 12 12"><circle cx="6" cy="6" r="5.3" fill="none" stroke="#555" stroke-width=".8"/><path d="M3.5 6h5M6.5 4l2 2-2 2" fill="none" stroke="#555" stroke-width=".8"/></svg></div>
</div>
<div class="abs card" style="left:476px">
  <div class="photo" role="img" aria-label="Cruise ship in a coastal harbor" style="background:radial-gradient(ellipse 35px 45px at 35px 75px,rgba(240,240,240,.9),transparent 70%),linear-gradient(180deg,#9dbbd8,#7c8f77 22%,#1f6ea6 45%,#0f4f86)"></div>
  <div class="label"><span>Other Destinations</span><svg width="12" height="12" viewBox="0 0 12 12"><circle cx="6" cy="6" r="5.3" fill="none" stroke="#555" stroke-width=".8"/><path d="M3.5 6h5M6.5 4l2 2-2 2" fill="none" stroke="#555" stroke-width=".8"/></svg></div>
</div>

<section class="about">
  <div class="abs about-photo" role="img" aria-label="Mother and two daughters walking hand in hand on the beach at sunset"></div>
  <h2 class="abs section-title" style="left:358px;top:738px;font-size:23px">About <em>Us</em></h2>
  <div class="abs rule" style="left:358px;top:773px;width:73px"></div>
  <p class="abs about-text">At Wanderbright Travel Co., we believe travel should be joyful, seamless, and filled with meaningful moments. What started as a passion for exploring the world has grown into a dedicated travel planning service focused on helping others experience the same excitement and wonder.</p>
  <a class="abs btn" href="#">Read More</a>
</section>

<footer>
  <div class="abs footer" role="img" aria-label="Dark navy overlay on palm tree beach scene"></div>
  <div class="abs foot-brand"><span class="brand-name" style="font-size:12px;text-align:center">Wanderbright<br>Travel Co.</span></div>
  <nav class="abs foot-nav">
    <span>Home</span><span>Brimwell Vacations</span><span>Family Trips</span><span>Texas Road Trips</span><span>Other Destinations</span><span>About Us</span>
  </nav>
  <div class="abs foot-contact" style="left:206px">
    <svg width="10" height="10" viewBox="0 0 24 24"><path fill="#fff" d="M6.6 10.8a15 15 0 0 0 6.6 6.6l2.2-2.2c.3-.3.7-.4 1-.2 1.1.4 2.3.6 3.6.6.6 0 1 .4 1 1V20c0 .6-.4 1-1 1A17 17 0 0 1 3 4c0-.6.4-1 1-1h3.5c.6 0 1 .4 1 1 0 1.3.2 2.5.6 3.6.1.3 0 .7-.2 1z"/></svg>
    <span>111.111.1111</span>
  </div>
  <div class="abs foot-contact" style="left:313px">
    <svg width="10" height="8" viewBox="0 0 20 14"><rect x="1" y="1" width="18" height="12" fill="none" stroke="#fff" stroke-width="1.6"/><path d="M1 1l9 7 9-7" fill="none" stroke="#fff" stroke-width="1.6"/></svg>
    <span>hello@wanderbrighttravel.com</span>
  </div>
  <div class="abs foot-rule"></div>
  <div class="abs social" style="left:63px;top:1180px"><span></span><span></span></div>
  <div class="abs copy">© 2026 Wanderbright Travel Co. All Rights Reserved.</div>
</footer>

</body>
</html>
```